Design a poster that illustrates the six central pillars of our school district's efforts with students. The attached PDF outlines the six main competencies we aim for students to possess upon graduation. Each of the 6 has 3 bullet points for the poster as well. The title is "Profile of a Trailblazer". Our mascot is this attached winged wheel. The overall concept is that staff take kids when they are young and develop these 6 things when they graduate. Our colors are navy, red, and white. We will make this poster in a variety of sizes in offices, classrooms, and in digital spaces as well. On the PDF - ignore the column that says "Synthesis". That has nothing to do with this poster.

The district is Harlow Creek Public Schools https://www.harlowcreek-schools.example/

```html
<!DOCTYPE html>
<html lang="en">
<head>
<meta charset="utf-8">
<title>Profile of a Trailblazer — Harlow Creek Public Schools</title>
<link rel="stylesheet" href="https://fonts.googleapis.com/css2?family=Outfit:wght@400;500&family=Nunito:wght@900&family=Montserrat:wght@800&family=Great+Vibes&display=swap">
<style>
  :root {
    --navy: #2b3a55;
    --navy-deep: #1f2b42;
    --red: #9a2229;
    --red-light: #ad2e35;
    --script-red: #c3222c;
    --white: #ffffff;
    --ink: #2d3342;
    --paper-soft: #f4f5f6;
  }
  * { box-sizing: border-box; }
  html, body {
    margin: 0; padding: 0;
    width: 984px; height: 1200px;
    overflow: hidden;
    background: var(--white);
  }
  .poster {
    position: relative;
    width: 984px; height: 1200px;
    overflow: hidden;
    background: var(--white);
    font-family: "Outfit", sans-serif;
    color: var(--ink);
  }
  .backdrop { position: absolute; inset: 0; }

  .brand { position: absolute; left: 100px; top: 42px; }
  .brand-mark {
    position: absolute; left: 0; top: 2px;
    width: 38px; height: 38px; border-radius: 50%;
    background: var(--red);
  }
  .brand-name {
    position: absolute; left: 54px; top: 0; white-space: nowrap;
    font-size: 19px; font-weight: 400; color: var(--navy); letter-spacing: 0.2px;
  }
  .brand-tagline {
    position: absolute; left: 54px; top: 26px; white-space: nowrap;
    font-size: 13px; font-weight: 400; color: var(--navy);
  }

  .title { position: absolute; left: 51px; top: 263px; width: 428px; height: 203px; margin: 0; text-align: center; }
  .title-line {
    position: absolute; left: 0; width: 100%;
    font-family: "Montserrat", sans-serif; font-weight: 800;
    font-size: 52px; line-height: 1; color: var(--white); letter-spacing: -1px;
  }
  .title-line.first { top: 36px; }
  .title-line.second { top: 100px; }
  .title-script {
    position: absolute; left: 0; width: 100%; top: 66px;
    font-family: "Great Vibes", cursive; font-size: 44px; line-height: 1;
    color: var(--script-red);
  }

  .pillar { position: absolute; }
  .pillar-head { position: relative; height: 92px; }
  .badge {
    position: absolute; left: 0; top: 0;
    width: 90px; height: 90px; border-radius: 50%;
    background: var(--navy);
    border: 2px solid var(--red);
    box-shadow: inset 0 0 0 3px var(--white);
    z-index: 2;
    display: flex; align-items: center; justify-content: center;
  }
  .badge svg { width: 46px; height: 46px; }
  .pillar-name {
    position: absolute; left: 78px; top: 28px; margin: 0;
    width: 276px; height: 35px; padding-left: 14px;
    border-radius: 0 18px 18px 0;
    background: linear-gradient(90deg, var(--red), var(--red-light));
    font-family: "Nunito", sans-serif; font-weight: 900;
    font-size: 27px; line-height: 35px; color: var(--white);
  }
  .points { position: absolute; top: 104px; left: 0; width: 450px; }
  .point {
    position: absolute; top: 0; margin: 0;
    width: 134px; min-height: 88px;
    padding-left: 20px;
    font-size: 12.6px; line-height: 16.2px; color: var(--ink);
    background: repeating-linear-gradient(to bottom, var(--red) 0 3px, transparent 3px 6px) no-repeat 6px 18px / 1px calc(100% - 18px);
  }
  .point::before {
    content: ""; position: absolute; left: 0; top: 2px;
    width: 13px; height: 13px; border-radius: 50%;
    border: 1.2px solid var(--red);
  }
  .point::after {
    content: ""; position: absolute; left: 5px; top: 4.5px;
    width: 3px; height: 6px;
    border-right: 1.2px solid var(--red); border-bottom: 1.2px solid var(--red);
    transform: rotate(45deg);
  }
  .point.col-1 { left: 0; }
  .point.col-2 { left: 144px; }
  .point.col-3 { left: 288px; }

  .communicator { left: 43px; top: 520px; }
  .adaptable { left: 514px; top: 520px; }
  .critical-thinker { left: 43px; top: 734px; }
  .collaborator { left: 522px; top: 734px; }
  .responsible { left: 43px; top: 961px; }
  .compassionate { left: 522px; top: 961px; }
  .adaptable .points { left: -1px; }
  .collaborator .points, .compassionate .points { left: -9px; }
</style>
</head>
<body>
<main class="poster">
  <svg class="backdrop" viewBox="0 0 984 1200" width="984" height="1200">
    <defs>
      <linearGradient id="sky" x1="0" y1="0" x2="0" y2="1">
        <stop offset="0" stop-color="#3a4154"/>
        <stop offset="0.22" stop-color="#7a5a52"/>
        <stop offset="0.36" stop-color="#f09a30"/>
        <stop offset="0.42" stop-color="#c9612a"/>
        <stop offset="0.55" stop-color="#4a2a1c"/>
        <stop offset="1" stop-color="#140e0c"/>
      </linearGradient>
      <linearGradient id="fade" x1="0" y1="0" x2="0" y2="1">
        <stop offset="0" stop-color="#eceef0"/>
        <stop offset="0.4" stop-color="#ffffff"/>
      </linearGradient>
    </defs>
    <rect role="img" aria-label="Sunset photograph: a graduate in cap and gown walking hand in hand with a young child across open land" x="0" y="0" width="984" height="660" fill="url(#sky)"/>
    <path d="M0,0 H533 C450,95 260,160 0,152 Z" fill="#f4f5f6"/>
    <path d="M0,395 C40,385 90,376 140,370 L140,378 C90,392 40,415 0,448 Z" fill="#9a2229"/>
    <path d="M0,440 C250,335 600,300 984,660 L984,1200 L0,1200 Z" fill="url(#fade)"/>
    <path d="M500,352 C700,340 900,480 984,560 L984,665 C880,500 700,370 500,352 Z" fill="#2b3a55"/>
    <path d="M51,318 Q51,263 106,263 H424 Q479,263 479,318 V411 Q479,466 424,466 H172 L120,499 L120,466 H106 Q51,466 51,411 Z" fill="#2b3a55"/>
  </svg>

  <header class="brand">
    <span class="brand-mark"></span>
    <span class="brand-name">Harlow Creek Public Schools</span>
    <span class="brand-tagline">Rooted in Learning, Rising in Character</span>
  </header>

  <h1 class="title">
    <span class="title-line first">PROFILE</span>
    <span class="title-script">of a</span>
    <span class="title-line second">TRAILBLAZER</span>
  </h1>

  <section class="pillar communicator">
    <div class="pillar-head">
      <div class="badge"><svg viewBox="0 0 48 48" fill="none" stroke="#fff" stroke-width="2" stroke-linejoin="round"><path d="M6 10h24v14H16l-6 5v-5H6z"/><path d="M34 18h8v12h-3v4l-5-4h-8v-3"/></svg></div>
      <h2 class="pillar-name">Communicator</h2>
    </div>
    <div class="points">
      <p class="point col-1">Expresses ideas clearly and respectfully (written &amp; verbal).</p>
      <p class="point col-2">Listens actively and understands diverse perspectives.</p>
      <p class="point col-3">Adjusts communication to suit the audience and context.</p>
    </div>
  </section>

  <section class="pillar adaptable">
    <div class="pillar-head">
      <div class="badge"><svg viewBox="0 0 48 48" fill="none" stroke="#fff" stroke-width="2" stroke-linecap="round"><path d="M38 20a15 15 0 0 0-27-6"/><path d="M10 8v6h6"/><path d="M10 28a15 15 0 0 0 27 6"/><path d="M38 40v-6h-6"/><circle cx="24" cy="24" r="5"/></svg></div>
      <h2 class="pillar-name">Adaptable</h2>
    </div>
    <div class="points">
      <p class="point col-1">Responds productively to new situations, challenges, and constructive feedback.</p>
      <p class="point col-2">Learns from new experiences and applies prior knowledge in an ever-changing world.</p>
      <p class="point col-3">Adjusts behavior and approach to engage effectively with diverse groups and environments.</p>
    </div>
  </section>

  <section class="pillar critical-thinker">
    <div class="pillar-head">
      <div class="badge"><svg viewBox="0 0 48 48" fill="none" stroke="#fff" stroke-width="2" stroke-linecap="round"><circle cx="21" cy="21" r="11"/><path d="M29 29l10 10"/><path d="M16 21h10M21 16v10"/></svg></div>
      <h2 class="pillar-name">Critical Thinker</h2>
    </div>
    <div class="points">
      <p class="point col-1">Questions, analyzes, and evaluates information from multiple sources.</p>
      <p class="point col-2">Identifies and solves complex problems creatively.</p>
      <p class="point col-3">Uses evidence and diverse perspectives to form reasoned conclusions and make informed decisions.</p>
    </div>
  </section>

  <section class="pillar collaborator">
    <div class="pillar-head">
      <div class="badge"><svg viewBox="0 0 48 48" fill="none" stroke="#fff" stroke-width="2"><circle cx="24" cy="12" r="5"/><circle cx="11" cy="34" r="5"/><circle cx="37" cy="34" r="5"/><path d="M21 16l-7 13M27 16l7 13M16 34h16"/></svg></div>
      <h2 class="pillar-name">Collaborator</h2>
    </div>
    <div class="points">
      <p class="point col-1">Demonstrates strong teamwork by contributing effectively and cooperatively toward shared goals.</p>
      <p class="point col-2">Listens actively and values diverse ideas and perspectives.</p>
      <p class="point col-3">Engages respectfully, knowing when to compromise, support, or take the lead.</p>
    </div>
  </section>

  <section class="pillar responsible">
    <div class="pillar-head">
      <div class="badge"><svg viewBox="0 0 48 48" fill="none" stroke="#fff" stroke-width="2" stroke-linecap="round" stroke-linejoin="round"><circle cx="24" cy="24" r="15"/><path d="M17 24l5 5 9-10"/></svg></div>
      <h2 class="pillar-name">Responsible</h2>
    </div>
    <div class="points">
      <p class="point col-1">Takes ownership of actions, choices, and commitments now and in future aspirations.</p>
      <p class="point col-2">Takes pride in managing time, resources, and self while striving to meet high expectations.</p>
      <p class="point col-3">Acts with integrity while advocating for themselves and others.</p>
    </div>
  </section>

  <section class="pillar compassionate">
    <div class="pillar-head">
      <div class="badge"><svg viewBox="0 0 48 48" fill="none" stroke="#fff" stroke-width="2" stroke-linejoin="round"><path d="M24 38S9 29 9 18a7.5 7.5 0 0 1 15-2 7.5 7.5 0 0 1 15 2c0 11-15 20-15 20z"/></svg></div>
      <h2 class="pillar-name">Compassionate</h2>
    </div>
    <div class="points">
      <p class="point col-1">Understands and acknowledges others' feelings, perspectives, and experiences.</p>
      <p class="point col-2">Responds with kindness, patience, empathy, and support.</p>
      <p class="point col-3">Seeks to connect with others, contribute positively to their community, and maintain their own well-being.</p>
    </div>
  </section>
</main>
</body>
</html>
```